TALMORK

The business want a professional looking business card. We have a scetch we will add but want the extra upgrade, and would like more suggestions for variations of our business cards.

```html
<!DOCTYPE html>
<html lang="en">
<head>
<meta charset="utf-8">
<title>TALMORK business cards</title>
<link rel="stylesheet" href="https://fonts.googleapis.com/css2?family=DM+Serif+Display&family=Poppins:wght@300;400;500&display=swap">
<style>
  :root {
    --backdrop: #2b2b2c;
    --paper: #f5f4f1;
    --copper: #b8692e;
    --copper-dark: #8f4a1c;
    --copper-light: #e3a866;
    --foil-hi: #f0c989;
  }
  * { margin: 0; padding: 0; box-sizing: border-box; }
  html, body { width: 1200px; height: 825px; overflow: hidden; background: var(--backdrop); }
  .canvas { position: relative; width: 1200px; height: 825px; }
  .card {
    position: absolute; left: 320px; width: 560px; height: 320px;
    background: var(--paper); border-radius: 14px; overflow: hidden;
    box-shadow: 0 6px 18px rgba(0,0,0,.35);
  }
  .card--front { top: 72px; }
  .card--back { top: 432px; }
  .card__art { position: absolute; inset: 0; width: 560px; height: 320px; }

  .brand { position: absolute; left: 0; width: 450px; top: 118px; text-align: center; color: var(--copper); font-family: "Poppins", sans-serif; }
  .brand__name { font-weight: 500; font-size: 30px; letter-spacing: 9px; padding-left: 9px; line-height: 1; }
  .brand__since { margin-top: 14px; font-weight: 500; font-size: 9px; letter-spacing: 4px; padding-left: 4px; }

  .person { position: absolute; left: 60px; top: 56px; color: var(--copper); }
  .person__name { font-family: "DM Serif Display", serif; font-size: 33px; line-height: 1; letter-spacing: .3px; }
  .person__role { margin-top: 12px; font-family: "Poppins", sans-serif; font-weight: 300; font-size: 20px; line-height: 1; }

  .contacts { position: absolute; left: 60px; top: 180px; list-style: none; font-family: "Poppins", sans-serif; font-size: 17px; color: var(--copper); }
  .contacts li { display: flex; align-items: center; height: 29px; }
  .contacts svg { width: 15px; height: 15px; margin-right: 10px; fill: none; stroke: var(--copper); stroke-width: 1.8; }

  .brand--small { position: absolute; left: 392px; top: 219px; font-family: "Poppins", sans-serif; font-weight: 500; font-size: 13px; letter-spacing: 3px; color: var(--copper); }
</style>
</head>
<body>
<main class="canvas">

  <section class="card card--front">
    <svg class="card__art" viewBox="0 0 560 320" aria-hidden="false">
      <defs>
        <linearGradient id="foil" x1="0" y1="0" x2="1" y2="1">
          <stop offset="0" stop-color="var(--foil-hi)"/>
          <stop offset=".45" stop-color="var(--copper-light)"/>
          <stop offset="1" stop-color="var(--copper-dark)"/>
        </linearGradient>
        <mask id="front-cut">
          <rect width="560" height="320" fill="#fff"/>
          <circle cx="153" cy="160" r="277" fill="#000"/>
        </mask>
      </defs>
      <rect class="foil-panel" width="560" height="320" fill="url(#foil)" mask="url(#front-cut)" role="img" aria-label="Copper foil panel with a white leaf sprig illustration"/>
      <circle cx="153" cy="160" r="289" fill="none" stroke="var(--paper)" stroke-width="1.6"/>
      <path d="M88 0 Q60 90 0 107" fill="none" stroke="var(--copper)" stroke-width="1"/>
    </svg>
    <div class="brand">
      <div class="brand__name">TALMORK</div>
      <div class="brand__since">SINCE 2026</div>
    </div>
  </section>

  <section class="card card--back">
    <svg class="card__art" viewBox="0 0 560 320">
      <defs>
        <mask id="back-cut">
          <rect width="560" height="320" fill="#fff"/>
          <circle cx="60" cy="-20" r="540" fill="#000"/>
        </mask>
      </defs>
      <rect class="foil-panel" width="560" height="320" fill="url(#foil)" mask="url(#back-cut)" role="img" aria-label="Copper foil corner with a small white leaf sprig illustration"/>
      <circle cx="60" cy="-20" r="528" fill="none" stroke="var(--copper)" stroke-width="1.4"/>
    </svg>

    <div class="person">
      <div class="person__name">Sindre Aasvoll Brekke</div>
      <div class="person__role">CEO &amp; Founder</div>
    </div>

    <ul class="contacts">
      <li>
        <svg viewBox="0 0 24 24"><path d="M5 3h4l2 5-3 2a12 12 0 0 0 6 6l2-3 5 2v4a2 2 0 0 1-2 2A18 18 0 0 1 3 5a2 2 0 0 1 2-2z"/></svg>
        004790516274
      </li>
      <li>
        <svg viewBox="0 0 24 24"><rect x="2" y="5" width="20" height="14" rx="1"/><path d="M2 6l10 7 10-7"/></svg>
        post@talmork.no
      </li>
      <li>
        <svg viewBox="0 0 24 24"><circle cx="12" cy="12" r="10"/><path d="M2 12h20M12 2a15 15 0 0 1 0 20M12 2a15 15 0 0 0 0 20"/></svg>
        www.talmork.no
      </li>
    </ul>

    <div class="brand--small">TALMORK</div>
  </section>

</main>
</body>
</html>
```